Design and Renovation Company Luxury Business Card

I want to create a luxury business card for a Design and Renovation Firm . We will use our current logo. The company name is 528BUILDA. We do not want anything standard. We need a very unique concept.
Please see uploaded inspiration. I really like the textured paper option. I would like the card to be thick with debossing, and/or embossing options. The logo has orange in it but I would like to see the card with and without the orange. I think the orange may make the company feel less high-end. The goal is to elevate the logo not match its vibe per se of the logo. We want something very unique, not standard at all!
I would like a space for :
Logo,
Name,
Position,
Email,
Office number,
Website Address,
Business Address,
Thank you!
Have fun!
Target Market(s)
Home owners Age 35 +
Industry/Entity Type
Design and Renovation
Contact Information for Business Card
Logo, Name, Position, Email, Office number, Website Address, Business Address,.
Colors
Designer to choose colors to be used in the design.
Requirements
Must have
- A luxury designer feel. Must be black or dark grey but open to other luxury ideas.
Nice to have
- Gold, silver, black embossing or debossing. Textured paper design.
Should not have
- A cheap look and feel.

```html
<!DOCTYPE html>
<html lang="en">
<head>
<meta charset="utf-8">
<title>528BUILDA Business Card</title>
<link rel="stylesheet" href="https://fonts.googleapis.com/css2?family=Roboto:wght@400;500;700&display=swap">
<style>
  :root {
    --backdrop: #141415;
    --card: #1e1e1f;
    --card-edge: #0c0c0c;
    --panel: #202021;
    --gold: #c9a55c;
    --gold-soft: #b8965a;
    --rule: rgba(255,255,255,0.18);
  }
  * { box-sizing: border-box; margin: 0; padding: 0; }
  html, body { width: 1200px; height: 1015px; overflow: hidden; }
  body {
    background: var(--backdrop);
    font-family: 'Roboto', Arial, sans-serif;
    display: flex; flex-direction: column; align-items: center; justify-content: center;
    gap: 44px;
  }
  .card {
    position: relative; width: 760px; height: 434px; overflow: hidden;
    background: radial-gradient(circle at 30% 30%, #232324, var(--card) 70%);
    box-shadow: 0 18px 40px rgba(0,0,0,0.6), 0 0 0 1px var(--card-edge);
  }
  .panel {
    position: absolute; background: var(--panel);
    box-shadow: inset 1px 1px 0 rgba(0,0,0,0.7), inset -1px -1px 0 rgba(255,255,255,0.07);
  }
  .hairline { position: absolute; height: 2px; background: var(--rule); }

  /* front */
  .brand {
    position: absolute; left: 70px; top: 140px;
    display: flex; align-items: center; gap: 14px;
    color: var(--gold); font-weight: 500; font-size: 46px; letter-spacing: 3px;
  }
  .brand-square { width: 30px; height: 30px; background: var(--gold); }

  /* back */
  .contact { position: absolute; left: 62px; top: 118px; color: var(--gold); }
  .contact-name { font-weight: 700; font-size: 25px; letter-spacing: 0.5px; }
  .contact-role { font-size: 18px; color: var(--gold-soft); margin-top: 2px; }
  .divider { width: 34px; height: 1px; background: var(--gold-soft); margin: 20px 0; }
  .contact-list { list-style: none; font-size: 18px; line-height: 1.45; }
  .contact-list li { display: flex; align-items: center; gap: 8px; }
  .contact-list svg { width: 15px; height: 15px; fill: var(--gold); flex: none; }
  .address { font-size: 18px; line-height: 1.35; margin-top: 18px; }
</style>
</head>
<body>
  <section class="card card-front">
    <div class="panel" style="left:450px;top:-2px;width:312px;height:138px"></div>
    <div class="hairline" style="left:540px;top:150px;width:222px"></div>
    <div class="panel" style="left:495px;top:172px;width:267px;height:118px"></div>
    <div class="panel" style="left:370px;top:232px;width:240px;height:204px"></div>
    <div class="brand"><span class="brand-square"></span>528BUILDA</div>
  </section>

  <section class="card card-back">
    <div class="panel" style="left:360px;top:-2px;width:402px;height:150px"></div>
    <div class="hairline" style="left:520px;top:168px;width:242px"></div>
    <div class="panel" style="left:670px;top:196px;width:92px;height:150px"></div>
    <div class="panel" style="left:430px;top:242px;width:222px;height:194px"></div>

    <div class="contact">
      <div class="contact-name">DANIEL HARPER</div>
      <div class="contact-role">Managing Director</div>
      <div class="divider"></div>
      <ul class="contact-list">
        <li><svg viewBox="0 0 16 16"><path d="M3.6 1.5l2.2 2.6-1.3 1.6c.9 2 2.8 3.9 4.8 4.8l1.6-1.3 2.6 2.2-1.3 2.1C7 13.5 2.5 9 1.5 3z"/></svg>044-987 654 321</li>
        <li><svg viewBox="0 0 16 16"><path d="M1 3h14v10H1zM2 4l6 5 6-5v-.2H2z"/></svg>hello@528builda.com</li>
        <li><svg viewBox="0 0 16 16"><path d="M8 1a7 7 0 100 14A7 7 0 008 1zm0 1.4c.8.8 1.5 2.3 1.8 4.1H6.2C6.5 4.7 7.2 3.2 8 2.4zM2.5 7.5h2.4c0 .9.1 1.7.3 2.5H3a5.6 5.6 0 01-.5-2.5zm4 0h3c0 .9-.1 1.7-.3 2.5H6.8a10 10 0 01-.3-2.5zm4.6 0h2.4c0 .9-.2 1.7-.5 2.5h-2.2c.2-.8.3-1.6.3-2.5zM8 13.6c-.6-.6-1.1-1.5-1.4-2.6h2.8c-.3 1.1-.8 2-1.4 2.6z"/></svg>www.528builda.com</li>
      </ul>
      <div class="divider"></div>
      <p class="address">87, Maple Court Lane<br>60318, Country Name</p>
    </div>
  </section>
</body>
</html>
```